Brimora - Nutritious Snacks and Desserts

We need a creative e-commerce website in which all features--buttons, background, etc.--convey our message: We sell delicious, nutritious snacks and desserts that most closely comply with the paleo diet guidelines. Our first product is Nuttaree®--raw, vegan, paleo chocolate balls that are made of dates, coconut, and cocoa. Our products are organic, raw, irresistible and nutritious. We have several versions of Nuttaree® in development, as well as mousse, ice cream, and crackers. Our mission is to purvey basic healthy foods. Our motto is, "Fuel for the Bold Trail-Walker(tm)."

Target Market(s)

Health-conscious professionals who tend to shop at health food stores. Our products also meet the requirements of a gluten-free diet; and they also don't contain refined sugar, so shoppers with gluten and possibly sugar issues are incidental customers.

Industry/Entity Type

Health Product

Coding

Number of Pages Required

5+ page

Colors

Designer to choose colors to be used in the design.

Requirements
Must have
• We need at least a home page, a products page, an about-us page, a contact page, and a shopping cart page. We would like to be able to add products on our own later. We should be able to handle some basic coding, especially if it's just a matter of copying and modifying product pages. We would also like the ability in the future to add blogging pages, allowing us to write articles about health food and healthy lifestyle, thus attracting web-traffic (SEO).
• Other features we would like to have:
• Product photo slider on the hopepage
• Back-to-top button at the bottom of the home page
• Make sure the site is mobile-compatible
• A search bar at the top of the homepage
• "Create an account" and "Previous orders"--allowing customers to see their previous orders and reorder what they purchased in the past.
Nice to have
• We would like to convey the paleo theme without actually stating it anywhere. We'll add text as necessary, according to the page layout; you can use ipsum lorem for purpose of demonstration.

```html
<!DOCTYPE html>
<html lang="en">
<head>
<meta charset="utf-8">
<title>Brimora – Nutritious Snacks and Desserts</title>
<link href="https://fonts.googleapis.com/css2?family=Lato:wght@400;700&family=Varela+Round&family=Playball&family=Alegreya:ital@1&display=swap" rel="stylesheet">
<style>
:root{
  --leaf:#7cc520;
  --leaf-bright:#86d01c;
  --moss:#3f7a0c;
  --moss-dark:#2f5f07;
  --stripe-a:#93cf54;
  --stripe-b:#88c647;
  --lime-text:#e8f21a;
  --panel:#3b5626;
  --ink:#555;
  --footer:#2f2f2f;
  --white:#fff;
}
*{margin:0;padding:0;box-sizing:border-box}
html,body{width:802px;height:1200px;overflow:hidden}
body{position:relative;font-family:"Lato",sans-serif;background:var(--stripe-a)}
.site-header{position:absolute;top:0;left:0;width:802px;height:83px;background:var(--white);z-index:5;box-shadow:0 1px 3px rgba(0,0,0,.25)}
.brand{position:absolute;left:52px;top:10px;display:flex;align-items:center;gap:10px}
.brand-mark{width:84px;height:84px;border-radius:50%;background:var(--leaf);border:4px solid var(--white);box-shadow:0 1px 3px rgba(0,0,0,.3)}
.brand-name{font-family:"Varela Round",sans-serif;font-size:36px;color:var(--leaf);margin-top:-22px}
.cart{position:absolute;right:52px;top:8px;display:flex;align-items:center;gap:8px;font-size:11px;color:var(--ink);padding-left:12px;border-left:1px solid #ccc;height:27px}
.main-nav{position:absolute;right:57px;top:47px;display:flex;gap:34px;font-size:13px;color:var(--ink)}
.main-nav .active{color:var(--leaf)}
.hero{position:absolute;top:83px;left:0;width:802px;height:420px;background:radial-gradient(ellipse at 50% 40%,#8a6a45 0%,#5d4329 55%,#3a2a1a 100%)}
.hero-title{position:absolute;top:222px;left:0;width:802px;text-align:center;font-family:"Varela Round",sans-serif;font-size:29px;font-weight:700;color:var(--lime-text);text-shadow:0 2px 3px rgba(0,0,0,.5);-webkit-text-stroke:.6px var(--lime-text)}
.hero-sub{position:absolute;top:265px;left:0;width:802px;text-align:center;font-size:11px;line-height:18px;color:var(--white);text-shadow:0 1px 2px rgba(0,0,0,.6)}
.stripes{position:absolute;top:420px;left:0;width:802px;height:560px;background:repeating-linear-gradient(90deg,var(--stripe-a) 0 25px,var(--stripe-b) 25px 50px)}
.hero-curve{position:absolute;top:420px;left:0}
.slider{position:absolute;left:70px;top:418px;width:661px;height:174px;border-radius:50px;background:var(--moss)}
.slider-inner{position:absolute;inset:8px;border:1.5px dashed rgba(255,255,255,.75);border-radius:44px}
.slide{position:absolute;top:28px;width:100px;text-align:center}
.slide-photo{height:68px;border-radius:6px;background:linear-gradient(135deg,#b47a46,#5a3520);margin:0 8px}
.slide-label{margin-top:12px;font-family:"Alegreya",serif;font-style:italic;font-size:14px;color:var(--white)}
.arrow{position:absolute;top:73px;width:24px;height:24px;border-radius:50%}
.arrow.prev{left:14px;background:var(--lime-text)}
.arrow.next{right:16px;background:#111}
.about-title{position:absolute;left:53px;top:628px;font-family:"Playball",cursive;font-size:30px;color:var(--white)}
.about-text{position:absolute;left:52px;top:674px;width:310px;font-size:9.6px;line-height:16.8px;color:var(--white)}
.about-link{position:absolute;left:53px;top:818px;font-family:"Playball",cursive;font-size:17px;color:var(--white)}
.feature{position:absolute;left:382px;top:634px;width:368px;height:208px;background:var(--panel);border:1px solid rgba(255,255,255,.5);border-radius:3px}
.feature-photo{position:absolute;left:26px;top:27px;width:152px;height:152px;border-radius:50%;background:radial-gradient(circle,#6b3d22 0%,#3a2517 60%,#1e2a12 100%)}
.feature-ribbon{position:absolute;left:16px;top:133px}
.feature-title{position:absolute;left:200px;top:32px;width:160px;font-size:11.5px;font-weight:700;line-height:17px;color:var(--lime-text)}
.feature-text{position:absolute;left:200px;top:68px;width:160px;font-size:9.6px;line-height:16.8px;color:var(--white)}
.footer-bg{position:absolute;top:900px;left:0}
.footer-mark{position:absolute;left:355px;top:893px;width:90px;height:90px;border-radius:50%;background:var(--leaf);border:5px solid var(--white);box-shadow:0 1px 4px rgba(0,0,0,.35)}
.footer-nav{position:absolute;top:1008px;left:0;width:802px;display:flex;justify-content:center;gap:14px;font-size:10px;color:var(--white)}
.contact{position:absolute;top:1060px;font-size:10px;line-height:17px;color:var(--white);display:flex;gap:8px;align-items:flex-start}
.rule{position:absolute;left:52px;top:1125px;width:698px;height:1px;background:rgba(255,255,255,.6)}
.copyright{position:absolute;left:53px;top:1155px;font-size:10px;color:var(--white)}
.social{position:absolute;top:1142px;width:32px;height:32px;border-radius:50%;border:1.5px solid var(--white)}
.social.filled{background:var(--leaf);border-color:var(--leaf)}
</style>
</head>
<body>
<header class="site-header">
  <div class="brand"><span class="brand-mark"></span><span class="brand-name">Brimora</span></div>
  <div class="cart">
    <svg width="26" height="26" viewBox="0 0 26 26"><path d="M8 10a5 5 0 0 1 10 0" fill="none" stroke="#7cc520" stroke-width="2"/><path d="M2 10h22l-3 14H5z" fill="#7cc520"/><text x="13" y="22" font-size="10" font-family="Lato,sans-serif" fill="#333" text-anchor="middle">1</text></svg>
    <span>( $ 0.00 )</span>
    <svg width="8" height="10" viewBox="0 0 8 10"><path d="M1 0l6 5-6 5z" fill="#7cc520"/></svg>
  </div>
  <nav class="main-nav"><span class="active">Home</span><span>About</span><span>Products</span><span>Blog</span><span>Contact</span></nav>
</header>

<section class="hero" role="img" aria-label="Close-up photo of nut-topped muffins on a wooden board with a checked napkin">
</section>
<div class="stripes"></div>
<svg class="hero-curve" width="802" height="80" viewBox="0 0 802 80"><path d="M0 50 Q0 0 60 0 H742 Q802 0 802 50 V80 H0Z" fill="none"/><path d="M0 0 H802 V70 Q700 20 401 20 Q100 20 0 70Z" fill="#5d4329" opacity="0"/><path d="M0 0 Q60 55 120 55 H680 Q742 55 802 0 V-1 H0Z" fill="#4a3522"/></svg>
<h1 class="hero-title">Fuel for the Bold Trail-Walker(tm)</h1>
<p class="hero-sub">Our products are raw, organic, vegan, gluten-free, dairy-free, fiber-rich, nutrient-dense, antioxidant-rich<br>real foods with no preservatives, no added sugar, and no artificial or plant-based sweeteners.</p>

<section class="slider">
  <div class="slider-inner"></div>
  <div class="arrow prev"><svg width="24" height="24" viewBox="0 0 24 24"><path d="M14 7l-5 5 5 5" fill="none" stroke="#111" stroke-width="2.5"/></svg></div>
  <div class="slide" style="left:56px"><div class="slide-photo" role="img" aria-label="Gift box of mixed nuts"></div><div class="slide-label">Lorem Ipsum</div></div>
  <div class="slide" style="left:167px"><div class="slide-photo" role="img" aria-label="Small box of chocolate truffles"></div><div class="slide-label">Lorem Ipsum</div></div>
  <div class="slide" style="left:281px"><div class="slide-photo" role="img" aria-label="Basket of colourful sweets"></div><div class="slide-label">Lorem Ipsum</div></div>
  <div class="slide" style="left:399px"><div class="slide-photo" role="img" aria-label="Open box of chocolate bites"></div><div class="slide-label">Lorem Ipsum</div></div>
  <div class="slide" style="left:510px"><div class="slide-photo" role="img" aria-label="Chocolate-dipped strawberries on a stand"></div><div class="slide-label">Lorem Ipsum</div></div>
  <div class="arrow next"><svg width="24" height="24" viewBox="0 0 24 24"><path d="M10 7l5 5-5 5" fill="none" stroke="#e8f21a" stroke-width="2.5"/></svg></div>
</section>

<h2 class="about-title">About Brimora Foods!</h2>
<p class="about-text">Lorem Ipsum is simply dummy text of the printing and typesetting industry. Lorem Ipsum has been the industry's standard dummy text ever since the 1500s, when an unknown printer took a galley of type and scrambled it to make a type specimen book. It has survived not only five centuries, but also the leap into electronic typesetting, remaining essentially unchanged. It was popularised in the 1960s with the release of Letraset sheets containing Lorem Ipsum passages.</p>
<p class="about-link">Learn More About Brimora Foods!</p>

<section class="feature">
  <div class="feature-photo" role="img" aria-label="Assorted chocolate truffles"></div>
  <svg class="feature-ribbon" width="178" height="40" viewBox="0 0 178 40"><path d="M10 0H168L178 20 168 40H10L0 20Z" fill="#86d01c"/><text x="89" y="26" text-anchor="middle" font-family="Varela Round,sans-serif" font-weight="700" font-size="14" fill="#fff">LOREM IPSUM DUMMY</text></svg>
  <h3 class="feature-title">LOREM IPSUM SIMMY TEXT TYPESETTING INDUSTRY.</h3>
  <p class="feature-text">Lorem Ipsum is simply dummy text of the printing and typesetting print industry. Lorem Ipsum has been the industry's standard dummy text of ever since the 1500s, when an to unknown printer took a galley .</p>
</section>

<svg class="footer-bg" width="802" height="300" viewBox="0 0 802 300" role="img" aria-label="Dark photo of frosted cupcakes with candy pieces"><defs><linearGradient id="ft" x1="0" y1="0" x2="0" y2="1"><stop offset="0" stop-color="#3c3c3c"/><stop offset="1" stop-color="#262626"/></linearGradient></defs><path d="M0 65 Q401 -40 802 65 V300 H0Z" fill="url(#ft)"/></svg>
<div class="footer-mark"></div>
<nav class="footer-nav"><span>Home</span><span>|</span><span>About</span><span>|</span><span>Products</span><span>|</span><span>Blog</span><span>|</span><span>Contact</span></nav>
<div class="contact" style="left:126px;top:1068px"><svg width="14" height="14" viewBox="0 0 14 14"><path d="M3 1l3 3-2 2q2 3 4 4l2-2 3 3-2 2Q5 13 1 3Z" fill="#7cc520"/></svg><span>+123-555-01942</span></div>
<div class="contact" style="left:296px"><svg width="11" height="15" viewBox="0 0 11 15"><path d="M5.5 15L1 7.5A5 5 0 1 1 10 7.5Z" fill="#7cc520"/><circle cx="5.5" cy="5" r="2" fill="#2f2f2f"/></svg><span>Lorem Ipsum is simply dummy<br>text of the printing dummy.</span></div>
<div class="contact" style="left:529px;top:1068px"><svg width="14" height="11" viewBox="0 0 14 11"><rect width="14" height="11" fill="#7cc520"/><path d="M0 0l7 6 7-6" fill="none" stroke="#2f2f2f" stroke-width="1.2"/></svg><span>hello@brimora-mail.com</span></div>
<div class="rule"></div>
<p class="copyright">BRIMORA | Copyright - 2018.All Rights Reserved</p>
<span class="social filled" style="left:644px" aria-label="Social link"></span>
<span class="social" style="left:682px" aria-label="Social link"></span>
<span class="social" style="left:720px" aria-label="Social link"></span>
</body>
</html>
```